Business Card Design For Office Furniture Clearance Company

Kestrel Office Clearance - our company name pretty much explains what we do, we clear offices for high end clients, mainly plc's and large international companies.

We require a nice looking business card that displays professionalism but without being too serious.

It would be nice to see just a little more than a conventional boring business card, make sure you add some flare.

Industry/Entity Type

Office Furniture

Contact Information for Business Card

CARD 1

Mark Holloway
Director
mark@kestrelofficeclearance.co.uk
m: 07700 153928

t: 01632 960418
www.kestrelofficeclearance.co.uk

Kestrel Office Clearance
Unit K4 B
2-8 Fenwick Lane
Brackenford
Northwold Vale
ZZ9 4QT

free office clearances… the easiest move you'll make.

CARD 2

Peter Radford
Director
peter@kestrelofficeclearance.co.uk
m: 07700 382615

t: 01632 960418

Kestrel Office Clearance
Unit K4 B
2-8 Fenwick Lane
Brackenford
Northwold Vale
ZZ9 4QT

Font styles to use
Sans Serif

Requirements
Must have
• A white background - as we have a blue logo.
Nice to have
• Nice use of the logo - play around with this and dissect it.

```html
<!DOCTYPE html>
<html lang="en">
<head>
<meta charset="utf-8">
<title>Kestrel Office Clearance – Business Card</title>
<link rel="stylesheet" href="https://fonts.googleapis.com/css2?family=Open+Sans:wght@400;600;700&display=swap">
<style>
  :root {
    --blue: #0a78c2;
    --blue-dark: #0b5f9c;
    --ink: #3a3a3a;
    --grey: #6b6b6b;
    --card-white: #ffffff;
    --card-black: #141414;
    --backdrop: #e9e7e3;
  }
  * { box-sizing: border-box; margin: 0; padding: 0; }
  html, body {
    width: 1200px; height: 900px; overflow: hidden;
    background: var(--backdrop);
    font-family: "Open Sans", sans-serif;
  }
  .stage { position: relative; width: 1200px; height: 900px; }

  .card {
    position: absolute;
    width: 600px; height: 364px;
    box-shadow: 0 6px 18px rgba(0,0,0,.18);
    overflow: hidden;
  }

  /* Back of card */
  .card--back { left: 530px; top: 60px; background: var(--card-black); }
  .brand-back {
    position: absolute; inset: 0;
    display: flex; flex-direction: column; align-items: center; justify-content: center; gap: 16px;
  }
  .brand-back .brand-dot {
    width: 150px; height: 150px; border-radius: 50%; background: var(--blue);
  }
  .brand-back .brand-name {
    color: var(--blue); font-weight: 700; font-size: 22px; letter-spacing: .3px;
  }

  /* Front of card */
  .card--front { left: 70px; top: 470px; background: var(--card-white); }
  .card-bands { position: absolute; inset: 0; }

  .person { position: absolute; left: 70px; top: 28px; }
  .person-name { color: var(--blue); font-weight: 700; font-size: 21px; line-height: 1.1; }
  .person-role { color: var(--grey); font-size: 12px; }

  .details { position: absolute; left: 34px; top: 100px; color: var(--ink); font-size: 14px; line-height: 1.3; }
  .company { color: var(--blue); font-weight: 700; font-size: 17px; line-height: 1.2; }
  .contact-list { list-style: none; margin-top: 2px; }
  .contact-list li { display: flex; align-items: center; gap: 8px; }
  .contact-list svg { width: 11px; height: 11px; fill: var(--blue); flex: none; }

  .tagline {
    position: absolute; left: 18px; top: 283px;
    color: var(--blue); font-weight: 700; font-size: 17px; white-space: nowrap;
  }

  .brand-front {
    position: absolute; left: 360px; top: 60px; width: 220px;
    display: flex; flex-direction: column; align-items: center; gap: 14px;
  }
  .brand-front .brand-dot {
    width: 140px; height: 140px; border-radius: 50%; background: var(--blue);
  }
  .brand-front .brand-name {
    color: var(--blue); font-weight: 700; font-size: 18px; text-align: center; white-space: nowrap;
  }
</style>
</head>
<body>
<main class="stage">

  <section class="card card--back" aria-label="Card back">
    <div class="brand-back">
      <span class="brand-dot"></span>
      <span class="brand-name">Kestrel Office Clearance</span>
    </div>
  </section>

  <section class="card card--front" aria-label="Card front">
    <svg class="card-bands" viewBox="0 0 600 364" width="600" height="364" aria-hidden="true">
      <rect x="0" y="26" width="52" height="46" fill="var(--blue-dark)"/>
      <polygon points="0,26 40,26 0,72" fill="var(--blue)"/>
      <line x1="40" y1="26" x2="0" y2="72" stroke="#fff" stroke-width="2"/>
      <polygon points="0,262 335,262 322,278 0,278" fill="var(--blue)"/>
      <polygon points="300,364 328,318 600,318 600,364" fill="var(--blue-dark)"/>
    </svg>

    <div class="person">
      <p class="person-name">Mark Holloway</p>
      <p class="person-role">Director</p>
    </div>

    <div class="details">
      <p class="company">Kestrel Office Clearance</p>
      <p>Unit K4 B, 2-8 Fenwick Lane</p>
      <p>Brackenford, Northwold Vale, ZZ9 4QT</p>
      <ul class="contact-list">
        <li><svg viewBox="0 0 12 12"><rect x="3" y="0" width="6" height="12" rx="1.2"/></svg>07700 153928</li>
        <li><svg viewBox="0 0 12 12"><path d="M2 0l3 3-1.5 1.5a7 7 0 0 0 4 4L9 7l3 3-2 2C5 12 0 7 0 2z"/></svg>01632 960418</li>
        <li><svg viewBox="0 0 12 12"><path d="M0 2h12v8H0z M0 2l6 4 6-4" stroke="#fff" stroke-width=".8"/></svg>mark@kestrelofficeclearance.co.uk</li>
        <li><svg viewBox="0 0 12 12"><circle cx="6" cy="6" r="6"/></svg>www.kestrelofficeclearance.co.uk</li>
      </ul>
    </div>

    <p class="tagline">free office clearances… the easiest move you'll make.</p>

    <div class="brand-front">
      <span class="brand-dot"></span>
      <span class="brand-name">Kestrel Office Clearance</span>
    </div>
  </section>

</main>
</body>
</html>
```